Moxy Fen needs some awesome stationary

Do you have what it takes to get my brand? You either do or you don't, have a crack at a design and you my just win my business.

I don't want to waste your or my time, so put your creative genius on either a business card or envelope.

I however need a package of stationary that follows the same brand. I will message you to complete the remaining should I like your first submission.

Here is what I need, have a go!

Basically I need the following for my small business based in melbourne.
- Letterhead (printer ready and MS Word)
- Business Card
- Compliments Slip
- Envelope
- Proposal Cover Page (MS Word only)
- Presentation Folder
- Marbled Fox Cards
- Student Name Tent
- Index Cards
- Vell-Ka

I am establishing the brand and it must be modern, professional but also relaxed; that is not formal and not corporate. It represents a company are leaders, but small enough to care and operate like a bunch of friends. We are bringing people and conversations back to business, and turfing out all the bureaucracy and crazy and wasteful procedures. Its about "lets talk and figure it out together and find even better ways".

Target Market(s)

Mainly companies that build software products, but Agile practices are used in many other industries (even graphic design projects)

Industry/Entity Type

Information Technology

Font styles to use
Sans Serif

Colors
3176b5
aaaaaa

Requirements
Must have
• I like curves and circles and not boxes or rectangles.
• I want a colour rich design with my brand colours, but it must be balanced.
• I want more modern than traditional, but simple modern
Should not have
• Not corporate
• Please don't waste my time if your not going to think about it.
• Don't mess with my primary logo
• Don't change my colours
• Don't overlay logo on image

```html
<!DOCTYPE html>
<html lang="en">
<head>
<meta charset="utf-8">
<title>Moxy Fen – Business Card</title>
<link href="https://fonts.googleapis.com/css2?family=Source+Sans+3:wght@400;600&display=swap" rel="stylesheet">
<style>
  :root {
    --brand-blue: #2c5aa0;
    --brand-grey: #949eab;
    --card-white: #ffffff;
    --backdrop: #e4e4e4;
    --ink-light: #ffffff;
  }
  * { margin: 0; padding: 0; box-sizing: border-box; }
  html, body {
    width: 1200px; height: 987px; overflow: hidden;
    background: var(--backdrop);
    font-family: "Source Sans 3", "Myriad Pro", Arial, sans-serif;
  }
  .stage { position: relative; width: 1200px; height: 987px; }
  .card {
    position: absolute; left: 293px; width: 615px; height: 352px;
    border-radius: 17px; overflow: hidden; background: var(--card-white);
  }
  .card--front { top: 130px; }
  .card--back { top: 505px; }
  .front-panel { position: absolute; inset: 0; width: 615px; height: 352px; }
  .contact { position: absolute; left: 32px; top: 0; color: var(--ink-light); }
  .contact__name { position: absolute; top: 63px; font-size: 22px; font-weight: 600; white-space: nowrap; }
  .contact__line { position: absolute; left: 1px; font-size: 15.5px; white-space: nowrap; line-height: 18px; }
  .contact__rule { position: absolute; left: 1px; width: 24px; height: 2px; background: var(--ink-light); }
  .contact__icon { position: absolute; left: 1px; width: 14px; height: 14px; }
  .contact__line--iconed { left: 25px; }
  .brand-name {
    position: absolute; left: 0; right: 0; top: 150px;
    display: flex; align-items: center; justify-content: center; gap: 14px;
  }
  .brand-name__dot { width: 26px; height: 26px; border-radius: 50%; background: var(--brand-blue); }
  .brand-name__text { font-size: 46px; font-weight: 600; color: var(--brand-blue); line-height: 1; }
</style>
</head>
<body>
<main class="stage">
  <section class="card card--front" aria-label="Business card front">
    <svg class="front-panel" viewBox="0 0 615 352" aria-hidden="true">
      <path d="M0 0 H470 C625 60 668 255 492 352 H0 Z" fill="var(--brand-grey)"/>
      <path d="M0 0 H457 C600 60 640 250 475 352 H0 Z" fill="var(--brand-blue)"/>
    </svg>
    <div class="contact">
      <p class="contact__name">Dale Orrin</p>
      <p class="contact__line" style="top:92px">CEO, Agile Coach &amp; Team Trainer</p>
      <p class="contact__line" style="top:113px">dale@moxyfen.com.au</p>
      <span class="contact__rule" style="top:141px"></span>
      <p class="contact__line" style="top:153px">PO Box 4417</p>
      <p class="contact__line" style="top:176px">Larkfield East</p>
      <p class="contact__line" style="top:197px">VIC 3190, Australia</p>
      <span class="contact__rule" style="top:223px"></span>
      <svg class="contact__icon" style="top:239px" viewBox="0 0 14 14" aria-hidden="true">
        <path d="M3 1 L5.5 1 L6.5 4 L5 5.2 C5.8 7 7 8.2 8.8 9 L10 7.5 L13 8.5 L13 11 C13 12 12 13 11 13 C5.5 12.6 1.4 8.5 1 3 C1 2 2 1 3 1 Z" fill="var(--ink-light)"/>
      </svg>
      <p class="contact__line contact__line--iconed" style="top:237px">1300MOXYFEN</p>
      <svg class="contact__icon" style="top:262px" viewBox="0 0 14 14" aria-hidden="true">
        <rect x="3" y="0.5" width="8" height="13" rx="1.5" fill="none" stroke="var(--ink-light)" stroke-width="1.6"/>
        <circle cx="7" cy="11" r="0.9" fill="var(--ink-light)"/>
      </svg>
      <p class="contact__line contact__line--iconed" style="top:261px">+61 412 555 018</p>
      <svg class="contact__icon" style="top:286px" viewBox="0 0 14 14" aria-hidden="true">
        <circle cx="7" cy="7" r="6.3" fill="var(--ink-light)"/>
        <path d="M4 3 C5.5 4 5 6 3.5 6.5 C3 8 5 9 5.5 10.5 M9 2.5 C8.5 4 10 5 11.5 5.5 M8.5 8 C9.5 9 10 10.5 9 12" stroke="var(--brand-blue)" stroke-width="1.3" fill="none"/>
      </svg>
      <p class="contact__line contact__line--iconed" style="top:284px">www.moxyfen.com.au</p>
    </div>
  </section>

  <section class="card card--back" aria-label="Business card back">
    <div class="brand-name">
      <span class="brand-name__dot"></span>
      <span class="brand-name__text">Moxy Fen</span>
    </div>
  </section>
</main>
</body>
</html>
```